Executive Business Card for Healthcare Company [Need Today]

I need a business card design for a healthcare company. The only branding the company has thus far is a logo. The cards will be utilized by company executives. The design I envision will be vibrant and appealing but with a corporate feel. They shouldn't be too casual or playful. I would like to complete this project TODAY if possible.

Target Market(s)

Healthcare vendors, other executives in healthcare and pharmaceuticals

Industry/Entity Type

Pharmaceutical

Contact Information for Business Card

See attachment

Font styles to use
Serif
Sans Serif

Colors

Designer to choose colors to be used in the design.

```html
<!DOCTYPE html>
<html lang="en">
<head>
<meta charset="UTF-8">
<title>Lumeva Therapeutics – Business Card</title>
<link href="https://fonts.googleapis.com/css2?family=Arimo:wght@400;700&display=swap" rel="stylesheet">
<style>
  :root {
    --bg: #e7e8e9;
    --card: #ffffff;
    --teal: #1aa6b7;
    --green: #45ad8a;
    --ink: #4a4a4a;
    --muted: #7a7a7a;
  }
  * { box-sizing: border-box; margin: 0; padding: 0; }
  html, body { width: 1200px; height: 726px; overflow: hidden; }
  body {
    background: var(--bg);
    font-family: "Arimo", Arial, sans-serif;
    position: relative;
  }
  .card {
    position: absolute;
    width: 525px;
    height: 300px;
    background: var(--card);
    overflow: hidden;
    box-shadow: 0 2px 10px rgba(0,0,0,0.12);
  }
  .card--front { left: 45px; top: 213px; }
  .card--back { left: 630px; top: 213px; }

  /* Front */
  .front-brand {
    position: absolute;
    left: 0; right: 0; top: 98px;
    display: flex;
    align-items: center;
    justify-content: center;
    gap: 16px;
  }
  .brand-dot {
    width: 58px; height: 58px;
    border: 3px solid var(--green);
    border-radius: 50%;
  }
  .brand-name {
    color: var(--teal);
    font-size: 30px;
    font-weight: 400;
    letter-spacing: 0.5px;
    line-height: 1.1;
  }
  .front-web {
    position: absolute;
    left: 0; right: 0; top: 218px;
    text-align: center;
    font-size: 13px;
    letter-spacing: 3px;
    color: var(--ink);
  }
  .front-web .domain { color: var(--teal); }

  /* Back */
  .back-ring {
    position: absolute;
    left: 285px; top: 18px;
    width: 270px; height: 270px;
    border: 6px solid var(--green);
    border-radius: 50%;
  }
  .back-tab {
    position: absolute;
    left: -22px; top: 148px;
    width: 40px; height: 40px;
    border-radius: 50%;
    background: var(--teal);
  }
  .back-brand {
    position: absolute;
    left: 34px; top: 58px;
    color: var(--teal);
    font-size: 24px;
    font-weight: 400;
    line-height: 1.15;
  }
  .person { position: absolute; left: 34px; top: 140px; }
  .person-name { color: var(--teal); font-size: 20px; font-weight: 400; }
  .person-title { color: var(--ink); font-size: 10px; margin-top: 4px; }
  .contact {
    position: absolute; left: 34px; top: 196px;
    list-style: none;
    font-size: 12px;
    color: var(--ink);
  }
  .contact li { display: flex; align-items: center; gap: 8px; height: 18px; }
  .contact svg { width: 11px; height: 11px; fill: var(--teal); flex: none; }
  .contact .accent { color: var(--teal); }
  .address { position: absolute; left: 34px; top: 258px; font-size: 12px; color: var(--ink); }
</style>
</head>
<body>
  <section class="card card--front">
    <div class="front-brand">
      <span class="brand-dot"></span>
      <span class="brand-name">Lumeva Therapeutics</span>
    </div>
    <p class="front-web">www.<span class="domain">lumevarx</span>.com</p>
  </section>

  <section class="card card--back">
    <div class="back-ring"></div>
    <div class="back-tab"></div>
    <p class="back-brand">Lumeva<br>Therapeutics</p>
    <div class="person">
      <p class="person-name">Daniel Hart</p>
      <p class="person-title">Senior Director of Marketing</p>
    </div>
    <ul class="contact">
      <li>
        <svg viewBox="0 0 12 12"><path d="M1 4c0-2 2-3 3-3l1 2-1 1c0 1 2 3 3 3l1-1 2 1c0 1-1 3-3 3C4 10 1 7 1 4z"/></svg>
        555-210-4417
      </li>
      <li>
        <svg viewBox="0 0 12 12"><path d="M3 0h6a1 1 0 0 1 1 1v10a1 1 0 0 1-1 1H3a1 1 0 0 1-1-1V1a1 1 0 0 1 1-1zm0 2v7h6V2z"/></svg>
        555-382-6054
      </li>
      <li>
        <svg viewBox="0 0 12 12"><circle cx="6" cy="6" r="5.5"/><path d="M0.5 6h11M6 0.5v11" stroke="#fff" stroke-width="0.9"/></svg>
        <span>dhart@<span class="accent">lumevarx</span>.com</span>
      </li>
    </ul>
    <p class="address">118 Market Street Dalton, GA 30720</p>
  </section>
</body>
</html>
```